Web site for a company that sells Pinball machines

We need a website that is an online shopping experience for a Store that sells pinball machines and accessories. The name of the store is called "Gadget Arcade." The store it self has a showroom, but we would also like to have an Internet e-commerce presence. We pinball machines made by Vexler pinball. You can visit their website and see their current list of machines as well as their website for the machines that we are going to carry in our store. Their website is Vexlerpinball.com. I am able to use their machine photos as well as their machine brochure PDF files. I am also able to use their logo on my website two list it as a Vexler Authorized Dealer.
This website design needs to be funky, fun, very technologically oriented and modern. The people buying machines our spending anywhere between $5000 and $15,000 on one machine. These Are high-end buyers who are also usually fairly tech savvy or at least enjoy technology and graphics.
Attachments: I have attached photographs of some of my own machines which may be used in the website. I've also attached some downloaded files from Vexler pinball.com as well as some of their PDF files for brochures. I will carry all of their current models they have listed under games. Not the archived games. I have included one of their machines called Thunderwolf Limited edition in my photograph attachments. The rest of the photos are just random pictures that I have taken myself and maybe used to build the site. Lastly I have attached my logo which I am not super crazy about so I will also be posting a contest to redesign this logo. Tons more of my own pinball photos are available.
I would like for people to be able to purchase machines and accessories from the website, but also inform them to our actual showroom.
Updates
Project Deadline Extended Reason: Hello. We have extended five days due to some complications during the construction of our actual building. We were unable to participate in this web design during this time and so unfortunately were not able give feedback appropriately. We are back on track and will provide feedback to the designers who have designed up until this point. We will still be interested in seeing new submissions, however; this extension will give us a chance to provide feedback and coordinate the website appropriately. Thank you so much for your submissions and your patience!!!!Gadget Arcade Added Friday, April 21, 2017
Target Market(s)
Target market is 16 to 75. Techy individuals to enjoy gaming technology video animation and Vegas style twinkle
Industry/Entity Type
It Company
Coding
Coded - Design and coding required
Number of Pages Required
3 page
Font styles to use
Look and feel
Each slider illustrates characteristics of the customer's brand and the style your logo design should communicate.

```html
<!DOCTYPE html>
<html lang="en">
<head>
<meta charset="utf-8">
<title>Gadget Arcade — Pinball Machines</title>
<link href="https://fonts.googleapis.com/css2?family=Roboto:wght@300;400;500;700;900&family=Roboto+Condensed:wght@400;700&display=swap" rel="stylesheet">
<style>
:root{
  --red:#e3231b;
  --red-dark:#a8130f;
  --blue:#1f74c9;
  --ink:#1b1b1d;
  --dark:#1e1e21;
  --darker:#141416;
  --gray:#e9e9ea;
  --mid:#8d8d92;
  --text:#555;
  --white:#fff;
  --gold:#f3a81b;
}
*{box-sizing:border-box;margin:0;padding:0}
html,body{width:1200px;height:2812px;overflow:hidden}
body{font-family:"Roboto",Arial,sans-serif;color:var(--text);background:var(--white);position:relative}
.abs{position:absolute}
a{color:inherit;text-decoration:none}

/* Header */
.hero{position:absolute;left:0;top:0;width:1200px;height:548px;
  background:radial-gradient(circle at 970px 250px,#ff4a2e 0,#c1160f 90px,#5a1208 200px,transparent 320px),
  radial-gradient(circle at 300px 400px,#3c6a35 0,transparent 260px),
  linear-gradient(120deg,#4b2a15 0%,#7a3c1a 35%,#3b1f2a 60%,#2a1210 100%)}
.hero::after{content:"";position:absolute;inset:0;background:linear-gradient(90deg,rgba(0,0,0,.45),rgba(0,0,0,0) 60%)}
.topbar{position:absolute;left:0;top:0;width:1200px;height:24px;background:rgba(10,10,12,.9);color:#cfcfcf;font-size:11px;z-index:3}
.topbar .contact{position:absolute;left:88px;top:6px;display:flex;gap:26px}
.topbar .contact span{display:flex;align-items:center;gap:6px}
.topbar .account{position:absolute;right:88px;top:6px}
.navbar{position:absolute;left:0;top:24px;width:1200px;height:62px;background:rgba(18,18,20,.82);z-index:3}
.brand{position:absolute;left:88px;top:14px;display:flex;align-items:center;gap:10px;color:var(--white);font-weight:700;font-size:20px;letter-spacing:.5px}
.brand i{width:30px;height:30px;border-radius:50%;background:var(--red);display:block}
.menu{position:absolute;left:320px;top:0;display:flex;height:62px}
.menu a{width:112px;height:62px;line-height:62px;text-align:center;color:var(--white);font-size:13px;font-weight:500;letter-spacing:.5px;border-top:4px solid var(--red)}
.menu a.active{background:var(--red)}
.search{position:absolute;left:1040px;top:22px}
.hero-copy{position:absolute;left:88px;top:96px;z-index:2}
.hero-copy .kicker{color:var(--red);font-weight:900;font-size:42px;letter-spacing:1px}
.hero-copy .offer{color:var(--white);font-weight:900;font-size:76px;line-height:1;margin-top:4px}
.hero-copy p{color:#eee;font-size:17px;line-height:22px;width:300px;margin-top:14px}
.btn{display:inline-block;background:var(--red);color:var(--white);font-size:12px;font-weight:700;border-radius:20px;padding:0 26px;height:34px;line-height:34px;letter-spacing:.5px}
.hero-copy .btn{margin-top:20px}

/* Section headings */
.section-title{position:absolute;left:0;width:1200px;text-align:center}
.section-title h2{font-family:"Roboto Condensed",Arial,sans-serif;font-weight:700;font-size:40px;color:var(--ink);letter-spacing:.5px;position:relative;display:inline-block}
.section-title h2::before{content:attr(data-ghost);position:absolute;left:-26px;top:-12px;color:rgba(0,0,0,.06);font-size:56px;white-space:nowrap}
.section-title p{font-size:12px;color:#888;width:420px;margin:8px auto 0;line-height:18px}

/* Best collection */
.collection{position:absolute;left:0;top:548px;width:1200px;height:512px;background:var(--white)}
.col-card{position:absolute;top:184px;width:248px;height:200px;overflow:hidden}
.col-card .shot{position:absolute;inset:0}
.col-card .tag{position:absolute;right:12px;top:18px;width:108px;height:104px;color:var(--white);padding:18px 12px;font-size:16px;font-weight:500;line-height:20px;text-align:center}
.col-card .tag small{display:block;font-size:11px;margin-top:14px;opacity:.9}
.tag.blue{background:rgba(31,116,201,.92)}
.tag.red{background:rgba(227,35,27,.92)}
.pager{position:absolute;left:0;width:1200px;display:flex;justify-content:center;gap:10px}
.pager span{width:54px;height:24px;border-radius:12px;background:var(--red);display:flex;align-items:center;justify-content:center}
.pager span.muted{background:#c9c9cc}

/* Top sellers */
.sellers{position:absolute;left:0;top:1060px;width:1200px;height:560px;background:var(--gray);
  background-image:radial-gradient(rgba(0,0,0,.05) 1px,transparent 1px);background-size:10px 10px}
.product{position:absolute;background:var(--white);border:1px solid #ddd;text-align:center}
.product .shot{margin:24px auto 0;width:150px;height:190px}
.product h3{font-size:19px;color:#333;font-weight:500;margin-top:16px}
.product .price{font-size:14px;margin-top:6px}
.product .price s{color:#aaa;margin-right:6px}
.product .price b{color:var(--red)}
.stars{color:var(--gold);font-size:13px;letter-spacing:1px;margin-top:4px}
.sale{position:absolute;left:-18px;top:-18px;width:46px;height:46px;border-radius:50%;background:var(--red);color:var(--white);font-size:12px;font-weight:700;line-height:46px;text-align:center}
.product.featured{background:#3a3a3e;border:none}
.icons{position:absolute;left:0;top:108px;width:320px;display:flex;justify-content:center;gap:8px}
.icons span{width:34px;height:34px;background:var(--white);display:flex;align-items:center;justify-content:center}

/* Video + news */
.media{position:absolute;left:0;top:1620px;width:1200px;height:620px;
  background:linear-gradient(180deg,rgba(170,18,12,.92),rgba(205,30,20,.9)),linear-gradient(90deg,#5a0f0a,#b81c12 50%,#6e120c)}
.media h2{position:absolute;top:68px;font-family:"Roboto Condensed",Arial,sans-serif;color:var(--white);font-size:38px;font-weight:700}
.media h2::after{content:"";position:absolute;left:0;bottom:-14px;width:60px;height:3px;background:var(--white)}
.video{position:absolute;left:88px;top:248px;width:480px;height:326px;background:radial-gradient(circle at 300px 130px,#ff5a3a,#9c130d 45%,#3a0907 100%)}
.play{position:absolute;left:190px;top:113px;width:100px;height:100px;border-radius:50%;border:4px solid var(--white);background:rgba(0,0,0,.3)}
.news{position:absolute;left:640px;width:480px;height:80px}
.news .thumb{position:absolute;left:0;top:0;width:80px;height:80px}
.news p{position:absolute;left:100px;top:2px;color:var(--white);font-size:14px;line-height:19px;width:360px}
.news .meta{position:absolute;left:100px;top:60px;color:#ffd9d4;font-size:12px}
.news .meta b{color:var(--gold);font-weight:400;margin-left:10px}

/* Testimonial */
.testimonial{position:absolute;left:88px;top:2280px;width:1024px;height:140px;border:1px solid #ccc;background:var(--white)}
.avatar{position:absolute;left:44px;top:20px;width:100px;height:100px;border-radius:50%;background:linear-gradient(#c9c2ba,#8a827a);border:4px solid #eee}
.divider{position:absolute;left:196px;top:26px;width:1px;height:88px;background:#ccc}
.quote{position:absolute;font-family:Georgia,serif;font-size:150px;color:#e6e6e6;line-height:1}
.testimonial .who{position:absolute;left:0;top:26px;width:1024px;text-align:center}
.who b{display:block;color:#333;font-size:16px;font-weight:500}
.who em{font-style:normal;font-size:11px;color:#999}
.testimonial p{position:absolute;left:330px;top:74px;width:520px;text-align:center;font-size:12px;color:#777;line-height:18px}

/* Footer */
.footer{position:absolute;left:0;top:2448px;width:1200px;height:364px;background:var(--dark);color:#bbb}
.footer h4{color:var(--white);font-size:16px;font-weight:500;margin-bottom:22px}
.f-about{position:absolute;left:88px;top:40px;width:220px}
.f-about .brand{position:static;margin-bottom:50px}
.f-about p{font-size:13px;line-height:19px}
.f-about .phone{display:flex;align-items:center;gap:8px;margin-top:16px;color:var(--white);font-size:14px}
.f-links{position:absolute;left:396px;top:80px}
.f-links li{list-style:none;font-size:13px;margin-bottom:14px;display:flex;align-items:center;gap:8px}
.f-links li::before{content:"";width:5px;height:5px;background:var(--red);display:block}
.f-blogs{position:absolute;left:600px;top:80px;width:260px}
.blog{display:flex;gap:12px;margin-bottom:14px}
.blog i{width:48px;height:40px;background:linear-gradient(135deg,#c22a1e,#4a1e16);display:block;flex:none}
.blog p{font-size:12px;line-height:16px;color:#ccc}
.blog small{display:block;font-size:10px;color:#888;margin-top:2px}
.f-social{position:absolute;left:924px;top:80px}
.f-social .row{display:grid;grid-template-columns:repeat(2,36px);gap:14px}
.f-social span{width:36px;height:36px;border-radius:50%;background:var(--white);display:block}
.copyright{position:absolute;left:0;bottom:0;width:1200px;height:40px;background:var(--darker);text-align:center;line-height:40px;font-size:12px;color:#888}
</style>
</head>
<body>

<header>
  <div class="hero" role="img" aria-label="Close-up photo of a pinball playfield with a red beacon light"></div>
  <div class="topbar">
    <div class="contact">
      <span><svg width="10" height="10" viewBox="0 0 24 24"><path fill="#e3231b" d="M6.6 10.8a15 15 0 0 0 6.6 6.6l2.2-2.2c.3-.3.7-.4 1-.2 1.1.4 2.3.6 3.6.6.6 0 1 .4 1 1V20c0 .6-.4 1-1 1A17 17 0 0 1 3 4c0-.6.4-1 1-1h3.5c.6 0 1 .4 1 1 0 1.3.2 2.5.6 3.6.1.3 0 .7-.2 1z"/></svg>1-555-010-4821</span>
      <span><svg width="10" height="10" viewBox="0 0 24 24"><circle cx="12" cy="12" r="9" fill="none" stroke="#e3231b" stroke-width="3"/></svg>24/7 Customer Care</span>
    </div>
    <div class="account">Login | Register</div>
  </div>
  <nav class="navbar">
    <div class="brand"><i></i>Gadget Arcade</div>
    <div class="menu">
      <a class="active" href="#">HOME</a><a href="#">ABOUT US</a><a href="#">GAMES</a><a href="#">COMMUNITY</a><a href="#">SUPPORT</a><a href="#">CONTACT US</a>
    </div>
    <svg class="search" width="16" height="16" viewBox="0 0 24 24"><circle cx="10" cy="10" r="7" fill="none" stroke="#fff" stroke-width="2.5"/><path d="M15 15l6 6" stroke="#fff" stroke-width="2.5"/></svg>
  </nav>
  <div class="hero-copy">
    <div class="kicker">LOREM IPSUM</div>
    <div class="offer">40% OFF</div>
    <p>It is a long established fact that a reader will be distracted by the readable content.</p>
    <a class="btn" href="#">SHOP NOW</a>
  </div>
</header>

<section class="collection">
  <div class="section-title" style="top:62px">
    <h2 data-ghost="BEST COLLECTION">BEST COLLECTION</h2>
    <p>It is a long established fact that a reader will be distracted by the readable content of a page when looking at its layout.</p>
  </div>
  <div class="col-card" style="left:88px"><div class="shot" role="img" aria-label="Pinball machine cabinet photo" style="background:linear-gradient(135deg,#d9362a,#f0b23a 55%,#6a1e16)"></div><div class="tag blue">LOREM IPSUM<small>$65.00</small></div></div>
  <div class="col-card" style="left:346px"><div class="shot" role="img" aria-label="Pinball machine cabinet photo" style="background:linear-gradient(135deg,#2b4a8a,#c73a2a 55%,#1a1a22)"></div><div class="tag blue">LOREM IPSUM<small>$65.00</small></div></div>
  <div class="col-card" style="left:604px"><div class="shot" role="img" aria-label="Pinball machine cabinet photo" style="background:linear-gradient(135deg,#b52a22,#2a2a30 55%,#d8a03a)"></div><div class="tag red">LOREM IPSUM<small>$65.00</small></div></div>
  <div class="col-card" style="left:862px"><div class="shot" role="img" aria-label="Pinball machine cabinet photo" style="background:linear-gradient(135deg,#c22d28,#3a6ab0 55%,#1c1c24)"></div><div class="tag blue">LOREM IPSUM<small>$65.00</small></div></div>
  <div class="pager" style="top:436px">
    <span><svg width="14" height="10" viewBox="0 0 14 10"><path d="M6 1L2 5l4 4M2 5h11" stroke="#fff" stroke-width="2" fill="none"/></svg></span>
    <span><svg width="14" height="10" viewBox="0 0 14 10"><path d="M8 1l4 4-4 4M12 5H1" stroke="#fff" stroke-width="2" fill="none"/></svg></span>
  </div>
</section>

<section class="sellers">
  <div class="section-title" style="top:42px">
    <h2 data-ghost="TOP SELLERS">TOP SELLERS</h2>
    <p>It is a long established fact that a reader will be distracted by the readable content of a page when looking at its layout.</p>
  </div>
  <div class="product" style="left:88px;top:150px;width:330px;height:290px">
    <div class="sale">Sale</div>
    <div class="shot" role="img" aria-label="Pinball machine product photo" style="background:linear-gradient(160deg,#3b3f8a,#1e2030 60%,#555)"></div>
    <h3>Nova Circuit</h3>
    <div class="price"><s>$19.00</s><b>$9.00</b></div>
    <div class="stars">★★★★☆</div>
  </div>
  <div class="product featured" style="left:440px;top:150px;width:320px;height:316px">
    <div class="shot" role="img" aria-label="Pinball machine product photo" style="width:170px;height:260px;background:linear-gradient(160deg,#5a5560,#2a2a2e 60%,#444)"></div>
    <div class="icons">
      <span><svg width="16" height="16" viewBox="0 0 24 24"><path d="M3 4h3l2 11h11l2-8H7" stroke="#333" stroke-width="2" fill="none"/><circle cx="10" cy="19" r="1.6" fill="#333"/><circle cx="17" cy="19" r="1.6" fill="#333"/></svg></span>
      <span><svg width="16" height="16" viewBox="0 0 24 24"><path d="M12 20S3 14 3 8.5A4.5 4.5 0 0 1 12 6a4.5 4.5 0 0 1 9 2.5C21 14 12 20 12 20z" fill="#e3231b"/></svg></span>
      <span><svg width="16" height="16" viewBox="0 0 24 24"><path d="M2 12s4-7 10-7 10 7 10 7-4 7-10 7S2 12 2 12z" stroke="#333" stroke-width="2" fill="none"/><circle cx="12" cy="12" r="3" fill="#333"/></svg></span>
    </div>
  </div>
  <div class="product" style="left:782px;top:150px;width:330px;height:290px">
    <div class="sale">Sale</div>
    <div class="shot" role="img" aria-label="Pinball machine product photo" style="background:linear-gradient(160deg,#8a2a30,#1e2030 60%,#555)"></div>
    <h3>Nova Circuit</h3>
    <div class="price"><s>$19.00</s><b>$9.00</b></div>
    <div class="stars">★★★★☆</div>
  </div>
  <div class="pager" style="top:496px">
    <span class="muted"><svg width="14" height="10" viewBox="0 0 14 10"><path d="M6 1L2 5l4 4M2 5h11" stroke="#fff" stroke-width="2" fill="none"/></svg></span>
    <span class="muted"><svg width="14" height="10" viewBox="0 0 14 10"><path d="M8 1l4 4-4 4M12 5H1" stroke="#fff" stroke-width="2" fill="none"/></svg></span>
  </div>
</section>

<section class="media">
  <h2 style="left:88px">LATEST VIDEO</h2>
  <h2 style="left:640px">LATEST NEWS</h2>
  <div class="video" role="img" aria-label="Video still of a lit pinball machine">
    <div class="play"><svg width="92" height="92" viewBox="0 0 92 92"><path d="M36 28l30 18-30 18z" fill="#fff"/></svg></div>
  </div>
  <div class="news" style="top:244px">
    <div class="thumb" role="img" aria-label="News photo of a pinball machine" style="background:linear-gradient(135deg,#f2b33a,#b8241a)"></div>
    <p>It is a long established fact that a reader will be distracted by the readable content of a page when looking at its layout.</p>
    <div class="meta">February 2017<b>★★★★☆</b></div>
  </div>
  <div class="news" style="top:340px">
    <div class="thumb" role="img" aria-label="News photo of a pinball machine" style="background:linear-gradient(135deg,#3a5fa8,#b8241a)"></div>
    <p>It is a long established fact that a reader will be distracted by the readable content of a page when looking at its layout.</p>
    <div class="meta">February 2017<b>★★★★☆</b></div>
  </div>
  <div class="news" style="top:440px">
    <div class="thumb" role="img" aria-label="News photo of a pinball machine" style="background:linear-gradient(135deg,#2a2a30,#c93a22)"></div>
    <p>It is a long established fact that a reader will be distracted by the readable content of a page when looking at its layout.</p>
    <div class="meta">February 2017<b>★★★★☆</b></div>
  </div>
</section>

<section class="testimonial">
  <div class="avatar" role="img" aria-label="Customer portrait"></div>
  <div class="divider"></div>
  <div class="quote" style="left:250px;top:10px">“</div>
  <div class="quote" style="right:40px;top:10px">”</div>
  <div class="who"><b>John Doe</b><em>Director</em></div>
  <p>It is a long established fact that a reader will be distracted by the readable content of a page when looking at its layout. The point of using this text is that it has a normal distribution.</p>
</section>

<footer class="footer">
  <div class="f-about">
    <div class="brand"><i></i>Gadget Arcade</div>
    <p>It is a long established fact that a reader will be distracted by the readable content.</p>
    <div class="phone"><svg width="14" height="14" viewBox="0 0 24 24"><path fill="#e3231b" d="M6.6 10.8a15 15 0 0 0 6.6 6.6l2.2-2.2c.3-.3.7-.4 1-.2 1.1.4 2.3.6 3.6.6.6 0 1 .4 1 1V20c0 .6-.4 1-1 1A17 17 0 0 1 3 4c0-.6.4-1 1-1h3.5c.6 0 1 .4 1 1 0 1.3.2 2.5.6 3.6.1.3 0 .7-.2 1z"/></svg>1-555-010-4821</div>
  </div>
  <div class="f-links">
    <h4>Quick Links</h4>
    <ul><li>Home</li><li>Shop</li><li>Blog</li><li>Page</li><li>Contact Us</li></ul>
  </div>
  <div class="f-blogs">
    <h4>Blogs</h4>
    <div class="blog"><i role="img" aria-label="Blog thumbnail"></i><p>It is a long established fact that a reader will be<small>February 2017</small></p></div>
    <div class="blog"><i role="img" aria-label="Blog thumbnail"></i><p>It is a long established fact that a reader will be<small>February 2017</small></p></div>
    <div class="blog"><i role="img" aria-label="Blog thumbnail"></i><p>It is a long established fact that a reader will be<small>February 2017</small></p></div>
  </div>
  <div class="f-social">
    <h4>Social Links</h4>
    <div class="row"><span></span><span></span><span></span><span></span></div>
  </div>
  <div class="copyright">hello@gadgetarcade.com © 2017. All rights reserved.</div>
</footer>

</body>
</html>
```